Redesign website for small print company

Vindurgata is a small printing company in Iceland mainly servicing Students, schools, etc. We are also doing all kind of other jobs, like business cards, book printing, brochure printing etc. We are also selling books online.
Our website is: www.vindurgata.is
What we are looking for is:
- Web Design (Uncoded - PSD layout only)
- Mobile friendly design, using our current color scheme: Red, green, yellow and light gray.
- Clean simple design
- Simple, light and easy to use.
- More menu Items/drop down
Industry/Entity Type
Digital Printing
Number of Pages Required
5+ page
Requirements
Must have
- Easy navigation
- Designed for mobile
- Current color scheme (see logo)
Nice to have
- Icon based products

```html
<!DOCTYPE html>
<html lang="en">
<head>
<meta charset="utf-8">
<title>Vindurgata – Full Service Printing</title>
<link href="https://fonts.googleapis.com/css2?family=Roboto:ital,wght@0,300;0,400;0,500;0,700;1,400&display=swap" rel="stylesheet">
<style>
:root{
  --red:#e3262b;
  --green:#116b35;
  --yellow:#f4d21c;
  --light:#efefef;
  --dark:#2a2727;
  --darker:#231f20;
  --text:#333;
  --muted:#666;
  --white:#fff;
}
*{box-sizing:border-box;margin:0;padding:0}
html,body{width:1200px;height:3448px;overflow:hidden}
body{font-family:'Roboto',sans-serif;color:var(--text);background:var(--white);position:relative}
.abs{position:absolute}
/* top bar */
.topbar{top:0;left:0;width:1200px;height:42px;background:#f6f6f6;font-size:13px;color:#444}
.topbar .item{position:absolute;top:12px;display:flex;align-items:center;gap:10px}
.topbar svg{width:14px;height:14px;fill:var(--green)}
.lang{position:absolute;right:140px;top:8px;width:120px;height:26px;background:#e4e4e4;font-size:12px;padding:6px 14px}
.lang:after{content:"";position:absolute;right:14px;top:10px;border:5px solid transparent;border-top-color:#333}
/* nav */
.nav{top:42px;left:0;width:1200px;height:68px;background:var(--white)}
.brand{position:absolute;left:140px;top:20px;display:flex;align-items:center;gap:10px;font-size:28px;font-weight:700;color:#222}
.brand i{width:26px;height:26px;background:var(--red);display:block}
.menu{position:absolute;top:24px;left:505px;display:flex;font-size:13px;font-weight:500;color:#222}
.menu span{margin-right:38px}
.menu .active{color:var(--red)}
.dropdown{top:92px;left:669px;width:180px;height:143px;background:var(--white);box-shadow:0 2px 8px rgba(0,0,0,.2);font-size:12px;z-index:5;padding-top:6px}
.dropdown div{height:35px;padding:10px 14px;border-bottom:1px solid #eee}
/* hero */
.hero{top:110px;left:0;width:1200px;height:534px;background:linear-gradient(135deg,#3a3536,#1c1a1a 60%,#2d2a2a)}
.hero-art{position:absolute;left:340px;top:100px;width:520px;height:240px;background:linear-gradient(120deg,#d8c9c0,#8c7a75 50%,#4a4a56);opacity:.85;border-radius:4px}
.hero h1{position:absolute;top:390px;width:1200px;text-align:center;color:var(--white);font-weight:500;font-size:36px;letter-spacing:.5px}
.hero h1 em{font-style:normal;color:var(--red);border-bottom:3px solid var(--red)}
/* section titles */
.title{position:absolute;width:1200px;left:0;text-align:center;font-size:34px;font-weight:700;color:#222}
.title.light{color:var(--white)}
.title b{color:var(--red)}
.rule{position:absolute;left:480px;width:240px;height:16px}
.rule:before{content:"";position:absolute;left:0;right:0;top:8px;height:1px;background:#999}
.rule i{position:absolute;left:111px;top:0;width:18px;height:16px;background:var(--yellow);border:3px solid var(--red)}
/* about */
.about-text{top:805px;left:140px;width:670px;font-size:13px;line-height:1.5;color:#333}
.about-text h3{font-size:16px;font-weight:700;margin-bottom:8px}
.about-text h3 b{color:var(--red)}
.about-text p{margin-bottom:18px}
.about-mark{top:821px;left:883px;width:175px;height:232px;background:var(--light);display:flex;align-items:center;justify-content:center;gap:10px;font-size:22px;font-weight:700;color:var(--green)}
.about-mark i{width:18px;height:18px;background:var(--red);display:block}
/* services */
.services{top:1118px;left:0;width:1200px;height:342px;background:linear-gradient(90deg,#2c2a2b,#3a3637 50%,#2a2828)}
.card{position:absolute;top:1279px;width:220px;height:287px;background:var(--white);box-shadow:0 2px 6px rgba(0,0,0,.25);text-align:center}
.card .photo{margin:14px 14px 0;height:112px}
.card h4{font-size:15px;font-weight:500;margin:20px 0 10px}
.card p{font-size:11px;line-height:1.45;padding:0 22px;color:#444}
.card .more{display:inline-block;margin-top:14px;border:1px solid var(--red);color:var(--red);font-size:10px;padding:6px 22px}
.arrow{position:absolute;width:44px;height:64px;display:flex;align-items:center;justify-content:center}
.arrow svg{width:18px;height:30px;fill:none;stroke:#fff;stroke-width:2}
.dots{position:absolute;left:0;width:1200px;display:flex;justify-content:center;gap:10px}
.dots i{width:10px;height:10px;border-radius:50%;background:#ddd;display:block}
.dots i.on{background:var(--green)}
/* products */
.product{position:absolute;top:1762px;width:215px;height:195px;background:var(--light);text-align:center}
.product .ico{margin:28px auto 14px;width:70px;height:70px;border-radius:50%;background:var(--white);display:flex;align-items:center;justify-content:center}
.product .ico svg{width:34px;height:34px}
.product h4{font-size:15px;font-weight:500;margin-bottom:6px}
.product h4.hot{color:var(--red)}
.product p{font-size:12px;line-height:1.35;padding:0 22px;color:#333}
.pager{position:absolute;top:1992px;width:32px;height:30px;display:flex;align-items:center;justify-content:center}
.pager svg{width:10px;height:16px;fill:none;stroke-width:2}
/* why */
.why{top:2095px;left:0;width:1200px;height:451px;background:linear-gradient(120deg,#262324,#3a3436 50%,#2a2627)}
.feature{position:absolute;width:430px;display:flex;gap:22px;color:var(--white)}
.feature .ico{flex:0 0 64px;height:64px;border-radius:50%;background:var(--white);display:flex;align-items:center;justify-content:center}
.feature .ico svg{width:32px;height:32px;fill:var(--green)}
.feature h4{font-size:15px;font-weight:500;margin-bottom:6px}
.feature p{font-size:12px;line-height:1.45;color:#ddd}
/* testimonial */
.quote{top:2678px;left:160px;width:880px;text-align:center;font-size:13px;font-style:italic;line-height:1.75;color:#333}
.author{top:2780px;left:0;width:1200px;text-align:center;color:var(--red);font-style:italic;font-weight:700;font-size:14px}
.avatar{top:2815px;left:570px;width:60px;height:60px;border:3px solid var(--green);background:linear-gradient(#8a8a7c,#4a4a3e)}
/* newsletter */
.newsletter{top:2935px;left:0;width:1200px;height:87px;background:var(--light)}
.newsletter .head{position:absolute;left:140px;top:22px;display:flex;align-items:center;gap:16px;font-size:22px;color:#222}
.newsletter .head span{width:42px;height:42px;border:2px solid #222;border-radius:50%;display:flex;align-items:center;justify-content:center}
.newsletter .field{position:absolute;left:512px;top:28px;width:380px;height:32px;background:var(--white);border:1px solid #ddd;font-size:11px;color:#999;padding:9px 10px}
.newsletter .btn{position:absolute;left:904px;top:28px;width:154px;height:32px;background:var(--red);color:var(--white);font-weight:700;font-size:14px;text-align:center;padding-top:8px}
/* footer */
.footer{top:3022px;left:0;width:1200px;height:359px;background:var(--darker);color:var(--white)}
.footer h5{position:absolute;top:60px;font-size:17px;font-weight:500}
.footer .inp{position:absolute;left:140px;width:242px;background:var(--white);font-size:11px;color:#999;padding:8px 8px}
.footer .send{position:absolute;left:140px;top:260px;width:88px;height:26px;background:var(--red);font-size:11px;font-weight:700;text-align:center;padding-top:6px}
.map{position:absolute;left:455px;top:96px;width:297px;height:190px;background:linear-gradient(135deg,#dfe6ec,#c9d6df)}
.find{position:absolute;left:826px;top:96px;font-size:12px;line-height:1.5}
.find .row{display:flex;gap:10px;margin-bottom:14px}
.find svg{flex:0 0 14px;height:14px;fill:var(--red);margin-top:2px}
.social{width:16px;height:16px;background:var(--white)}
.bottom{top:3381px;left:0;width:1200px;height:67px;background:var(--red);color:var(--white);font-size:11px}
.bottom p{position:absolute;left:140px;top:27px}
.card-badge{position:absolute;top:22px;width:40px;height:24px;background:var(--white);border-radius:3px}
</style>
</head>
<body>

<div class="abs topbar">
  <div class="item" style="left:150px"><svg viewBox="0 0 24 24"><path d="M6.6 10.8a15.1 15.1 0 006.6 6.6l2.2-2.2c.3-.3.7-.4 1-.2 1.1.4 2.3.6 3.6.6.6 0 1 .4 1 1V20c0 .6-.4 1-1 1A17 17 0 013 4c0-.6.4-1 1-1h3.5c.6 0 1 .4 1 1 0 1.3.2 2.5.6 3.6.1.3 0 .7-.2 1z"/></svg>555 2740</div>
  <div class="item" style="left:383px"><svg viewBox="0 0 24 24"><path d="M2 5h20v14H2zm2 2v.5l8 5 8-5V7z"/></svg>verk@vindurgata.is</div>
  <div class="item" style="left:673px"><svg viewBox="0 0 24 24"><path d="M12 2a10 10 0 100 20 10 10 0 000-20zm1 10.4l4 2.4-.8 1.3L11 13V6h2z"/></svg>Mon - Fri: 9-17</div>
  <div class="lang">Language</div>
</div>

<div class="abs nav">
  <div class="brand"><i></i>VINDURGATA</div>
  <div class="menu">
    <span>HOME</span><span>ABOUT US</span><span class="active">SERVICES ⌄</span><span>PRODUCTS</span><span>JOB SUBMIT</span><span>CONTACT US</span>
  </div>
</div>
<div class="abs dropdown">
  <div>Bookprinting</div><div>Better Finances</div><div>Photocopying</div><div style="border:0">Spiral-bound books</div>
</div>

<section class="abs hero">
  <div class="hero-art" role="img" aria-label="Printed books, magazines and business cards arranged on a desk"></div>
  <h1>FULL <em>SERVICE PRINTING</em> WITH A SMAILE.</h1>
</section>

<!-- About -->
<h2 class="title" style="top:702px"><b>A</b>BOUT US</h2>
<div class="rule" style="top:750px"><i></i></div>
<div class="abs about-text">
  <h3><b>W</b>elcome to University</h3>
  <p>University education is a company located in the campus, which has specialized in the service of school staff, as well as providing general public printing.</p>
  <p>Higher education publishes seminars and first-class textbooks for courses, prints theses for lesson, as well as working on an unprecedented number of smaller pieces for students, teachers and organizations. These include brochures, reports, questionnaires, business cards, books, OCR scanning and more.</p>
  <p>Higher education is a tailored print shop, The Heron is the official eco-label of the Nordic countries, which has created a foothold in this country and is known among consumers.</p>
  <p>University education is located at the corner of Birkigata and Hlíðargata. (walked into Hlíðargötumegin)</p>
</div>
<div class="abs about-mark"><i></i>Vindurgata</div>

<!-- Services -->
<section class="abs services">
  <div class="arrow" style="left:76px;top:232px;background:#555"><svg viewBox="0 0 18 30"><path d="M15 2L3 15l12 13"/></svg></div>
  <div class="arrow" style="left:1080px;top:232px;background:var(--green)"><svg viewBox="0 0 18 30"><path d="M3 2l12 13L3 28"/></svg></div>
</section>
<h2 class="title light" style="top:1176px"><b>O</b>UR SERVICES</h2>
<div class="rule" style="top:1224px"><i></i></div>

<div class="card" style="left:140px"><div class="photo" role="img" aria-label="Desk calendar with photos" style="background:linear-gradient(135deg,#e9ecef,#9aa3aa)"></div><h4>Calander Printing</h4><p>A calander with own photos is a great Christmas gift. You can use our design tool to upload your own.</p><span class="more">READ MORE</span></div>
<div class="card" style="left:375px"><div class="photo" role="img" aria-label="Pink notebook with glasses" style="background:linear-gradient(135deg,#f6d6d0,#e58f86)"></div><h4>Book Printing</h4><p>A calander with own photos is a great Christmas gift. You can use our design tool to upload your own.</p><span class="more">READ MORE</span></div>
<div class="card" style="left:609px"><div class="photo" role="img" aria-label="Hand holding a blank business card" style="background:linear-gradient(135deg,#3a3a3a,#111)"></div><h4>Business Cards</h4><p>A calander with own photos is a great Christmas gift. You can use our design tool to upload your own.</p><span class="more">READ MORE</span></div>
<div class="card" style="left:842px"><div class="photo" role="img" aria-label="Poster prints with plants on a desk" style="background:linear-gradient(135deg,#f1efe9,#9fae8a)"></div><h4>A0 Posters Printing</h4><p>A calander with own photos is a great Christmas gift. You can use our design tool to upload your own.</p><span class="more">READ MORE</span></div>
<div class="dots" style="top:1587px"><i class="on"></i><i></i><i></i></div>

<!-- Products -->
<h2 class="title" style="top:1660px"><b>O</b>UR PRODUCTS</h2>
<div class="rule" style="top:1708px"><i></i></div>

<div class="product" style="left:140px"><div class="ico"><svg viewBox="0 0 34 34"><path d="M4 26l14-18 12 6-14 16z" fill="var(--red)"/><path d="M4 26l12 4" stroke="#a01a1e" stroke-width="2"/></svg></div><h4 class="hot">Brochures</h4><p>Lorem ipsum dolor sit amet, consectetur adipis elit</p></div>
<div class="product" style="left:375px"><div class="ico"><svg viewBox="0 0 34 34"><path d="M9 16h16l-2 14H11z" fill="var(--green)"/><path d="M12 16l-3-10M17 16V4M22 16l4-10" stroke="var(--green)" stroke-width="2"/></svg></div><h4>Stationary</h4><p>Lorem ipsum dolor sit amet, consectetur adipis elit</p></div>
<div class="product" style="left:609px"><div class="ico"><svg viewBox="0 0 34 34"><rect x="7" y="4" width="20" height="26" rx="2" fill="none" stroke="var(--green)" stroke-width="2.5"/><path d="M11 11h12M11 16h12M11 21h8" stroke="var(--green)" stroke-width="2"/></svg></div><h4>Books</h4><p>Lorem ipsum dolor sit amet, consectetur adipis elit</p></div>
<div class="product" style="left:842px"><div class="ico"><svg viewBox="0 0 34 34"><path d="M4 14l13-9 13 9v16H4z" fill="var(--green)"/><path d="M17 13c-2-3-6 0-3 3l3 3 3-3c3-3-1-6-3-3z" fill="#fff"/></svg></div><h4>Greeting cards</h4><p>Lorem ipsum dolor sit amet, consectetur adipis elit</p></div>

<div class="pager" style="left:524px;background:#e2e2e2"><svg viewBox="0 0 10 16" stroke="#999"><path d="M8 2L2 8l6 6"/></svg></div>
<div class="dots" style="top:2002px;width:auto;left:574px"><i class="on"></i><i></i><i></i></div>
<div class="pager" style="left:642px;background:var(--green)"><svg viewBox="0 0 10 16" stroke="#fff"><path d="M2 2l6 6-6 6"/></svg></div>

<!-- Why choose us -->
<section class="abs why" role="img" aria-label="Colour swatch fan in dark tones">
  <div class="feature" style="left:143px;top:187px"><div class="ico"><svg viewBox="0 0 24 24"><path d="M3 7l9-4 9 4v10l-9 4-9-4z"/></svg></div><div><h4>Over 200k Orders Completed</h4><p>It is a long established fact that a reader will be distracted by the readable content of a page when looking at its layout.</p></div></div>
  <div class="feature" style="left:642px;top:187px"><div class="ico"><svg viewBox="0 0 24 24"><circle cx="12" cy="7" r="3.5"/><circle cx="5" cy="10" r="2.5"/><circle cx="19" cy="10" r="2.5"/><path d="M5 21c0-4 3-7 7-7s7 3 7 7zM0 20c0-3 2-5 5-5v5zM24 20c0-3-2-5-5-5v5z"/></svg></div><div><h4>Great Customer Service</h4><p>It is a long established fact that a reader will be distracted by the readable content of a page when looking at its layout.</p></div></div>
  <div class="feature" style="left:143px;top:304px"><div class="ico"><svg viewBox="0 0 24 24"><path d="M6 3h12l4 6-10 12L2 9z"/></svg></div><div><h4>Superior Quality and Value</h4><p>It is a long established fact that a reader will be distracted by the readable content of a page when looking at its layout.</p></div></div>
  <div class="feature" style="left:642px;top:304px"><div class="ico"><svg viewBox="0 0 24 24"><path d="M12 2a10 10 0 100 20 10 10 0 000-20zm1 10.4l4 2.4-.8 1.3L11 13V6h2z"/></svg></div><div><h4>Fast Turnaround</h4><p>It is a long established fact that a reader will be distracted by the readable content of a page when looking at its layout.</p></div></div>
</section>
<h2 class="title light" style="top:2158px"><b>W</b>HY CHOOSE US ?</h2>
<div class="rule" style="top:2206px"><i></i></div>

<!-- Testimonial -->
<h2 class="title" style="top:2610px"><b>T</b>ESTIMONIAL</h2>
<div class="rule" style="top:2655px"><i></i></div>
<p class="abs quote">Lorem ipsum dolor sit amet, consectetur adipiscing elit, sed do eiusmod tempor incididunt ut labore et dolore magna aliqua. Ut enim  veniam, quis nostrud exercitation ullamco laboris nisi ut aliquip ex ea commodo consequat. Duis aute irure dolor in reprehenderit in voluptate velit esse cillum dolore eu fugiat nulla pariatur. Excepteur sint occaecat cupidatat non proident, sunt in culpa qui officia .</p>
<p class="abs author">- Sconsectetur adipiscing</p>
<div class="abs avatar" role="img" aria-label="Customer portrait"></div>
<div class="arrow" style="left:76px;top:2760px;background:#e6e6e6"><svg viewBox="0 0 18 30" style="stroke:#aaa"><path d="M15 2L3 15l12 13"/></svg></div>
<div class="arrow" style="left:1080px;top:2760px;background:var(--green)"><svg viewBox="0 0 18 30"><path d="M3 2l12 13L3 28"/></svg></div>
<div class="dots" style="top:2897px"><i class="on"></i><i></i><i></i></div>

<!-- Newsletter -->
<div class="abs newsletter">
  <div class="head"><span><svg width="22" height="16" viewBox="0 0 22 16"><path d="M1 1h20v14H1zM1 1l10 8 10-8" fill="none" stroke="#222" stroke-width="2"/></svg></span>Sign Up For Newsletter</div>
  <div class="field">Enter your email here</div>
  <div class="btn">SUBSCRIBE</div>
</div>

<!-- Footer -->
<footer class="abs footer">
  <h5 style="left:140px">Drop us a line</h5>
  <div class="inp" style="top:96px;height:30px">Name</div>
  <div class="inp" style="top:136px;height:30px">Email</div>
  <div class="inp" style="top:176px;height:70px">Message</div>
  <div class="send">SEND</div>
  <h5 style="left:455px">Location Map</h5>
  <div class="map" role="img" aria-label="Street map showing the shop location"></div>
  <h5 style="left:826px">Find Us</h5>
  <div class="find">
    <div class="row"><svg viewBox="0 0 24 24"><path d="M12 2a7 7 0 00-7 7c0 5 7 13 7 13s7-8 7-13a7 7 0 00-7-7zm0 9.5a2.5 2.5 0 110-5 2.5 2.5 0 010 5z"/></svg><span>48 Harbor Lane<br>Lakeview, Oregon 97630-2214</span></div>
    <div class="row"><svg viewBox="0 0 24 24"><path d="M6.6 10.8a15.1 15.1 0 006.6 6.6l2.2-2.2c.3-.3.7-.4 1-.2 1.1.4 2.3.6 3.6.6.6 0 1 .4 1 1V20c0 .6-.4 1-1 1A17 17 0 013 4c0-.6.4-1 1-1h3.5c.6 0 1 .4 1 1 0 1.3.2 2.5.6 3.6.1.3 0 .7-.2 1z"/></svg><span>555 2740</span></div>
    <div class="row"><svg viewBox="0 0 24 24"><path d="M2 5h20v14H2zm2 2v.5l8 5 8-5V7z"/></svg><span>verk@vindurgata.is</span></div>
    <div class="social"></div>
  </div>
</footer>
<div class="abs bottom">
  <p>Copyright © 2018 NORTHBEAM STUDIO. All Rights Reserved</p>
  <div class="card-badge" style="left:978px"></div>
  <div class="card-badge" style="left:1022px"></div>
</div>

</body>
</html>
```